Homemaking training schools needs a Business Card design

Designer, Hello!

No special requirements, good-looking enough.
--------------------------------------------------------------------------

Name: Marcus Dole
Chairman
Tel: 0574-71948263
Mobile: 13857420916
Email: kelvora@mailnest.example
Web: www.prt2019.example
Add: No.258, LanpingJie, BeiyuanQu, Ningbo, Zhejiang

LOGO
Ningbo PRT Homemaking Training School

Target Market(s)

pregnant women, mothers, infants, the elderly and families, including cleaning, cooking, nursing training.

Industry/Entity Type

Business

Contact Information for Business Card

Name: Marcus Dole
Chairman
Tel: 0574-71948263
Mobile: 13857420916
Email: kelvora@mailnest.example
Web: www.prt2019.example

LOGO

Font styles to use
Serif
Sans Serif
Decorative

Requirements
Nice to have
• Feels: clean, specifications, safety, comfort, warmth and happiness.

```html
<!DOCTYPE html>
<html lang="en">
<head>
<meta charset="utf-8">
<title>PingRuiTang Business Card</title>
<link rel="stylesheet" href="https://fonts.googleapis.com/css2?family=Lato:wght@400;700&display=swap">
<style>
  :root {
    --blue: #3a7bbf;
    --magenta: #c4168f;
    --ink: #2b2b2b;
    --white: #ffffff;
    --backdrop: #e9eaec;
  }
  * { margin: 0; padding: 0; box-sizing: border-box; }
  html, body { width: 1200px; height: 900px; overflow: hidden; }
  body {
    background: var(--backdrop);
    font-family: "Lato", Arial, sans-serif;
    position: relative;
  }
  .card {
    position: absolute;
    left: 280px;
    width: 640px;
    height: 366px;
    background: var(--white);
    overflow: hidden;
    box-shadow: 0 6px 18px rgba(0,0,0,0.18);
  }
  .card--back { top: 64px; }
  .card--front { top: 466px; }

  .brand { position: absolute; text-align: center; }
  .brand__row { display: flex; align-items: center; justify-content: center; gap: 12px; }
  .brand__dot { width: 16px; height: 16px; border-radius: 50%; background: var(--magenta); }
  .brand__name { font-weight: 700; color: var(--blue); letter-spacing: 0.5px; }
  .brand__tagline { color: var(--ink); letter-spacing: 1px; }

  .card--back .brand { left: 0; right: 0; top: 112px; }
  .card--back .brand__name { font-size: 52px; line-height: 1; }
  .card--back .brand__tagline { font-size: 20px; margin-top: 10px; }
  .card--back .site { position: absolute; left: 0; right: 0; top: 248px; text-align: center;
    font-size: 15px; letter-spacing: 3px; color: var(--ink); font-weight: 700; }

  .card--front .brand { left: 36px; top: 34px; text-align: left; }
  .card--front .brand__row { justify-content: flex-start; }
  .card--front .brand__name { font-size: 40px; line-height: 1; }
  .card--front .brand__tagline { font-size: 16px; margin-top: 8px; }

  .card__bg { position: absolute; inset: 0; }

  .address { position: absolute; left: 24px; top: 234px; color: var(--white);
    font-size: 15px; line-height: 1.45; font-style: normal; }

  .contact { position: absolute; right: 16px; top: 214px; text-align: right; color: var(--white); }
  .contact__name { font-size: 22px; line-height: 1.1; }
  .contact__title { font-size: 15px; color: var(--magenta); margin-bottom: 6px; }
  .contact__list { list-style: none; }
  .contact__item { display: flex; justify-content: flex-end; align-items: center; gap: 8px;
    font-size: 16px; line-height: 23px; }
  .contact__icon { width: 14px; height: 14px; flex: none; }
</style>
</head>
<body>

<section class="card card--back">
  <div class="brand">
    <div class="brand__row">
      <span class="brand__name">PingRuiTang</span>
      <span class="brand__dot"></span>
    </div>
    <p class="brand__tagline">Training &amp; Services</p>
  </div>
  <p class="site">www.prt2019.example</p>
</section>

<section class="card card--front">
  <svg class="card__bg" viewBox="0 0 640 366" width="640" height="366" aria-hidden="true">
    <path class="swoosh" d="M0,150 C205,250 430,244 640,6 L640,366 L0,366 Z" fill="var(--magenta)"/>
    <path class="band" d="M0,150 C200,250 420,250 640,30 L640,366 L0,366 Z" fill="var(--blue)" stroke="var(--white)" stroke-width="3"/>
  </svg>

  <div class="brand">
    <div class="brand__row">
      <span class="brand__name">PingRuiTang</span>
      <span class="brand__dot"></span>
    </div>
    <p class="brand__tagline">Training &amp; Services</p>
  </div>

  <address class="address">
    No.258, LanpingJie<br>
    BeiyuanQu, Ningbo, Zhejiang
  </address>

  <div class="contact">
    <p class="contact__name">Marcus Dole</p>
    <p class="contact__title">Chairman</p>
    <ul class="contact__list">
      <li class="contact__item">0574-71948263
        <svg class="contact__icon" viewBox="0 0 14 14" aria-label="Telephone"><path d="M3 1 L5 1 L6 4 L4.5 5.2 Q5.8 8.2 8.8 9.5 L10 8 L13 9 L13 11 Q13 13 11 13 Q2 12 1 3 Q1 1 3 1 Z" fill="var(--magenta)"/></svg>
      </li>
      <li class="contact__item">1385-7420916
        <svg class="contact__icon" viewBox="0 0 14 14" aria-label="Mobile"><rect x="3.5" y="0.5" width="7" height="13" rx="1.5" fill="none" stroke="var(--magenta)" stroke-width="1.4"/><circle cx="7" cy="11" r="0.9" fill="var(--magenta)"/></svg>
      </li>
      <li class="contact__item">kelvora@mailnest.example
        <svg class="contact__icon" viewBox="0 0 14 14" aria-label="Email"><rect x="0.5" y="2.5" width="13" height="9" fill="var(--magenta)"/><path d="M1 3 L7 8 L13 3" fill="none" stroke="var(--blue)" stroke-width="1.2"/></svg>
      </li>
      <li class="contact__item">www.prt2019.example
        <svg class="contact__icon" viewBox="0 0 14 14" aria-label="Website"><circle cx="7" cy="7" r="6" fill="var(--magenta)"/><path d="M1 7 H13 M7 1 V13 M7 1 Q3 7 7 13 M7 1 Q11 7 7 13" fill="none" stroke="var(--blue)" stroke-width="0.9"/></svg>
      </li>
    </ul>
  </div>
</section>

</body>
</html>
```